Request for Business Card Design

Hi. My name is Marlene, I am looking for a new business card design for my company, Quarrow Signal Instruments, LLC. I really like the design you did for Tarsel Venture and was hoping you could do something similar using our full logo and our mark. I am also open to any raised texture design using our mark. I have attached our full logo, which would need to be somewhere on the card, as well as the mark in both outline and full form, as well as our brand colors / guide. The card does not have to be white, as long as our logo and mark appear. I actually like darker colored business cards more, but am open to all options. If you are interested in working with me, please let me know. We would also take the business card design into letterhead design if you can do that.

```html
<!DOCTYPE html>
<html lang="en">
<head>
<meta charset="UTF-8">
<title>Quarrow Signal Instruments – Business Card</title>
<link href="https://fonts.googleapis.com/css2?family=Barlow:wght@600&family=Open+Sans:wght@400;700&display=swap" rel="stylesheet">
<style>
  :root {
    --backdrop: #3b3b3b;
    --card: #161616;
    --card-deep: #0d0d0d;
    --pattern-light: #3a3a3a;
    --accent: #1a9ad6;
    --ink: #ffffff;
    --ink-soft: #e6e6e6;
  }
  * { box-sizing: border-box; margin: 0; padding: 0; }
  html, body {
    width: 1200px; height: 801px; overflow: hidden;
    background: var(--backdrop);
  }
  .stage {
    width: 1200px; height: 801px;
    display: flex; align-items: center; justify-content: center; gap: 60px;
  }
  .card {
    position: relative;
    width: 525px; height: 300px;
    background: var(--card);
    border-bottom: 3px solid var(--accent);
    box-shadow: 0 10px 30px rgba(0,0,0,.35);
    overflow: hidden;
  }
  .wordmark {
    display: flex; align-items: center; gap: 14px;
    font-family: "Barlow", sans-serif; font-weight: 600; color: var(--ink);
    letter-spacing: 0.06em; line-height: 1;
  }
  .wordmark-dot {
    width: 46px; height: 46px; border-radius: 50%;
    background: var(--accent); flex: none;
  }
  .wordmark-name { font-size: 34px; display: block; }
  .wordmark-sub { font-size: 11.5px; display: block; margin-top: 5px; letter-spacing: 0.04em; }

  /* front */
  .card-front .wordmark { position: absolute; left: 38px; top: 126px; }
  .divider {
    position: absolute; left: 292px; top: 0; height: 232px;
    border-left: 2px solid var(--accent);
  }
  .contact {
    position: absolute; left: 312px; top: 34px;
    font-family: "Open Sans", sans-serif; color: var(--ink-soft);
    font-size: 13px; line-height: 1.4;
  }
  .contact-name {
    font-weight: 700; color: var(--accent); font-size: 19px;
    letter-spacing: 0.03em; text-transform: uppercase; line-height: 1.1;
  }
  .contact-title { margin-bottom: 16px; }
  .contact-address { margin-bottom: 16px; }
  .contact-line { display: flex; align-items: center; gap: 8px; }
  .contact-line svg { width: 11px; height: 11px; fill: var(--accent); flex: none; }

  /* back */
  .texture {
    position: absolute; inset: 0;
    background: linear-gradient(120deg, var(--card-deep) 0%, var(--card) 45%, var(--pattern-light) 100%);
  }
  .card-back .wordmark { position: absolute; left: 132px; top: 150px; }
</style>
</head>
<body>
<main class="stage">
  <section class="card card-front" aria-label="Card front">
    <div class="wordmark">
      <span class="wordmark-dot"></span>
      <span><span class="wordmark-name">QUARROW</span><span class="wordmark-sub">SIGNAL INSTRUMENTS</span></span>
    </div>
    <div class="divider"></div>
    <div class="contact">
      <p class="contact-name">Orin Vasquell</p>
      <p class="contact-title">President</p>
      <p class="contact-address">1820 Linden Cove Road<br>Harlow Bay CA 90417</p>
      <p class="contact-line">
        <svg viewBox="0 0 12 12"><path d="M2.5 0.5 L4.5 0.5 L5.2 3.2 L3.8 4.3 Q5 7 7.7 8.2 L8.8 6.8 L11.5 7.5 L11.5 9.5 Q11 11.5 9 11.5 Q0.5 10.5 0.5 3 Q0.5 1 2.5 0.5 Z"/></svg>
        555-014-2278
      </p>
      <p class="contact-line">
        <svg viewBox="0 0 12 12"><path d="M0.5 2.5 H11.5 V10 H0.5 Z M0.5 2.5 L6 6.8 L11.5 2.5" stroke="#161616" stroke-width="0.9"/></svg>
        o.vasquell@quarrow.com
      </p>
      <p class="contact-line">
        <svg viewBox="0 0 12 12"><circle cx="6" cy="6" r="5.5"/><path d="M0.5 6 H11.5 M6 0.5 Q2.8 6 6 11.5 M6 0.5 Q9.2 6 6 11.5" stroke="#161616" stroke-width="0.9" fill="none"/></svg>
        www.quarrow.com
      </p>
    </div>
  </section>

  <section class="card card-back" aria-label="Card back">
    <div class="texture" role="img" aria-label="Raised gloss texture of the brand mark repeated across the card"></div>
    <div class="wordmark">
      <span class="wordmark-dot"></span>
      <span><span class="wordmark-name">QUARROW</span><span class="wordmark-sub">SIGNAL INSTRUMENTS</span></span>
    </div>
  </section>
</main>
</body>
</html>
```